Business Cards used to invite people to our church

We are a church and have need of a business card sized advertisement that allows our members to hand them out in order to invite people to the church. I need the front of the card to say "You're Invited" or "Come Check us out". with the service times on the back of the card later.
I have attached one of the OLD cards we have used in the past, but we want a complete makeover, into a more modern style that does not require the image.
I am also replacing the old logo with a newer "flat" logo which is attached.
Please use marketing colors. (blue or red or something that catches attention)
Create a card that DOES NOT have the picture of the two people on the front
The information on the sample card back is correct to go onto new card
Target Market(s)
anyone
Industry/Entity Type
Business
Contact Information for Business Card
sertice times and address information which you can get from the sample card I uploaded. It should have "You're Invited" or "Come Check us out" on the front of the card with out logo.

```html
<!DOCTYPE html>
<html lang="en">
<head>
<meta charset="UTF-8">
<title>Grace Harbor Fellowship – Invitation Cards</title>
<link rel="stylesheet" href="https://fonts.googleapis.com/css2?family=Open+Sans:ital,wght@0,600;0,700;1,700&family=Pinyon+Script&display=swap">
<style>
  :root {
    --red: #ff0000;
    --white: #ffffff;
    --stripe: #f0f0f0;
    --backdrop: #d9d9d9;
    --card-edge: rgba(0,0,0,0.18);
  }
  * { box-sizing: border-box; margin: 0; padding: 0; }
  html, body {
    width: 1200px; height: 900px; overflow: hidden;
    background: var(--backdrop);
    font-family: "Open Sans", Arial, sans-serif;
  }
  .canvas {
    position: relative; width: 1200px; height: 900px;
  }
  .card {
    position: absolute; left: 320px;
    width: 560px; height: 320px;
    background: var(--red);
    color: var(--white);
    overflow: hidden;
    box-shadow: 0 6px 18px var(--card-edge);
  }
  .card--back { top: 100px; }
  .card--front { top: 480px; }

  /* Back side */
  .service-times {
    position: absolute; top: 22px; left: 225px; width: 290px;
    font-style: italic; font-weight: 700; font-size: 13px; line-height: 21px;
  }
  .service-times li { display: flex; align-items: baseline; list-style: none; }
  .service-times .leader {
    flex: 1; border-bottom: 2px dotted var(--white); margin: 0 4px; transform: translateY(-4px);
  }
  .brand {
    position: absolute; top: 110px; left: 0; width: 100%;
    display: flex; justify-content: center; align-items: center; gap: 12px;
  }
  .brand__dot { width: 18px; height: 18px; border-radius: 50%; background: var(--white); }
  .brand__name { font-weight: 600; font-size: 26px; letter-spacing: 2px; text-transform: uppercase; }
  .stripe { position: absolute; left: 0; width: 100%; background: var(--stripe); }
  .card--back .stripe--upper { top: 205px; height: 12px; }
  .card--back .stripe--lower { top: 290px; height: 12px; }
  .contact {
    position: absolute; top: 235px; left: 24px; right: 24px;
    display: flex; justify-content: space-between;
    font-weight: 700; font-size: 14px;
  }
  .contact span { display: flex; align-items: center; gap: 8px; }
  .contact svg { width: 13px; height: 13px; fill: var(--white); }
  .contact__phone { margin-top: 22px; }

  /* Front side */
  .invite {
    position: absolute; top: 60px; left: 60px; width: 470px;
    font-family: "Pinyon Script", cursive; font-size: 64px; line-height: 64px;
  }
  .invite__line1 { display: block; padding-left: 120px; }
  .invite__line2 { display: block; }
  .card--front .stripe--upper { top: 250px; height: 16px; }
</style>
</head>
<body>
<main class="canvas">

  <section class="card card--back" aria-label="Card back">
    <ul class="service-times">
      <li><span>Sunday</span><span class="leader"></span><span>9:00 Am</span></li>
      <li><span>Sunday</span><span class="leader"></span><span>11.00 Am</span></li>
      <li><span>Web. Bible Class</span><span class="leader"></span><span>7:00 Pm</span></li>
    </ul>
    <div class="brand">
      <span class="brand__dot"></span>
      <span class="brand__name">Grace Harbor Fellowship</span>
    </div>
    <div class="stripe stripe--upper"></div>
    <div class="contact">
      <span class="contact__address">
        <svg viewBox="0 0 24 24"><path d="M12 2a7 7 0 0 0-7 7c0 5 7 13 7 13s7-8 7-13a7 7 0 0 0-7-7zm0 9.5A2.5 2.5 0 1 1 12 6.5a2.5 2.5 0 0 1 0 5z"/></svg>
        2480 Cedar Lane - Brookfield, Tx 75200
      </span>
      <span class="contact__phone">
        <svg viewBox="0 0 24 24"><path d="M6.6 10.8a15 15 0 0 0 6.6 6.6l2.2-2.2a1 1 0 0 1 1-.25 11.4 11.4 0 0 0 3.6.57 1 1 0 0 1 1 1V20a1 1 0 0 1-1 1A17 17 0 0 1 3 4a1 1 0 0 1 1-1h3.5a1 1 0 0 1 1 1c0 1.25.2 2.45.57 3.6a1 1 0 0 1-.25 1z"/></svg>
        1-800-555-0142
      </span>
    </div>
    <div class="stripe stripe--lower"></div>
  </section>

  <section class="card card--front" aria-label="Card front">
    <h1 class="invite">
      <span class="invite__line1">Come</span>
      <span class="invite__line2">Check us out</span>
    </h1>
    <div class="stripe stripe--upper"></div>
  </section>

</main>
</body>
</html>
```